Brenwick Structures Construction Company Seeking Modern Website

We are a small construction company wanting to create a web presence. We don't have much in the way of current content but will get photos as they come in. Attached is a picture of our business card.
The pages we would like on the menu are:
Home
Portfolio
Product Specs
Testimonials
Our Process
Contact
Some designs we like are:
http://www.tovasheds-example.com/
http://www.qrnstructures-example.com/
http://dunholtbarns-example.com/
http://pellingframes-example.com/
Not much requirements other than that so feel free to be creative!
Updates
Target Market(s)
Construction
Commercial and Residential Buildings
Industry/Entity Type
Construction Company
Number of Pages Required
5+ page
Look and feel

```html
<!DOCTYPE html>
<html lang="en">
<head>
<meta charset="utf-8">
<title>Brenwick Structures</title>
<link href="https://fonts.googleapis.com/css2?family=Open+Sans:wght@400;600;700&display=swap" rel="stylesheet">
<style>
  :root {
    --ink: #0c0d10;
    --sky: #1aa6e0;
    --sky-deep: #1685c3;
    --accent-red: #d4262b;
    --paper: #ffffff;
    --mist: #f2f2f2;
    --footer: #333333;
    --footer-text: #e6e6e6;
    --dot: #5a5a5a;
  }
  * { margin: 0; padding: 0; box-sizing: border-box; }
  html, body { width: 941px; height: 1200px; overflow: hidden; }
  body { font-family: "Open Sans", Arial, sans-serif; background: var(--paper); position: relative; color: var(--paper); }

  .site-header { position: absolute; top: 0; left: 0; width: 941px; height: 62px; background: var(--ink); border-bottom: 3px solid var(--sky); z-index: 3; }
  .main-nav a { position: absolute; top: 22px; font-size: 12px; color: var(--paper); text-decoration: none; }
  .brand-mark { position: absolute; left: 360px; width: 221px; top: 15px; text-align: center; font-size: 20px; line-height: 28px; font-weight: 700; color: var(--sky); white-space: nowrap; }

  .hero { position: absolute; top: 62px; left: 0; width: 941px; height: 420px;
    background: linear-gradient(180deg, #8e9cab 0%, #b9c0c7 22%, #cfd0ce 42%, #e6e4e0 58%, #c49a6c 72%, #a97543 86%, #7d5130 100%); }
  .hero-arrow { position: absolute; top: 258px; z-index: 2; }

  .welcome { position: absolute; top: 482px; left: 0; width: 941px; height: 199px; text-align: center;
    background: linear-gradient(180deg, var(--sky) 0%, var(--sky-deep) 100%); }
  .welcome h1 { margin-top: 22px; font-size: 19px; line-height: 26px; font-weight: 400; letter-spacing: 0.3px; }
  .welcome h2 { margin-top: 1px; font-size: 12.5px; line-height: 18px; font-weight: 400; }
  .welcome p { width: 750px; margin: 11px auto 0; font-size: 8.4px; line-height: 16px; }
  .btn-outline { display: inline-block; margin-top: 18px; width: 111px; height: 31px; line-height: 28px; border: 1.5px solid #5fd0f5; font-size: 12px; color: var(--paper); text-decoration: none; }

  .services { position: absolute; top: 681px; left: 0; width: 941px; height: 190px; background: var(--paper); }
  .service-tile { position: absolute; top: 26px; width: 383px; height: 135px; }
  .service-tile.commercial { left: 77px; background: linear-gradient(90deg, #3d74cf 0%, #5d6772 38%, #4f5966 50%, #3c6fcb 72%, #6b97dc 100%); }
  .service-tile.residential { left: 480px; background: linear-gradient(90deg, #8a6948 0%, #5a4f44 30%, #3c3c3c 60%, #4a4d48 80%, #6d7268 100%); }
  .service-label { position: absolute; left: 0; width: 100%; top: 83px; text-align: center; line-height: 1.15; text-shadow: 0 1px 2px rgba(0,0,0,.4); }
  .service-label .big { font-size: 18px; display: block; }
  .service-label .small { font-size: 14px; display: block; }

  .galleries { position: absolute; top: 871px; left: 0; width: 941px; height: 207px; background: var(--mist); }
  .galleries h3 { position: absolute; top: 18px; width: 941px; text-align: center; font-size: 19px; font-weight: 400; color: var(--accent-red); }
  .gallery-item { position: absolute; top: 67px; width: 176px; height: 111px; }
  .g1 { left: 77px; background: linear-gradient(135deg, #eef2f5 0%, #d2dbe2 60%, #e2c86a 100%); }
  .g2 { left: 280px; background: linear-gradient(180deg, #b7d0e8 0%, #a9a49a 55%, #7c6a58 100%); }
  .g3 { left: 484px; background: linear-gradient(180deg, #a9c0dc 0%, #9ea5ad 55%, #5f8f3e 100%); }
  .g4 { left: 687px; background: linear-gradient(135deg, #f2e8e1 0%, #dcb59c 70%, #c9473f 100%); }

  .site-footer { position: absolute; top: 1078px; left: 0; width: 941px; height: 122px; background: var(--footer); border-top: 3px solid var(--accent-red); color: var(--footer-text); }
  .footer-brand { position: absolute; left: 77px; top: 22px; font-size: 19px; font-weight: 700; color: var(--sky); }
  .footer-nav { position: absolute; right: 77px; top: 24px; font-size: 10px; }
  .footer-nav a { color: var(--footer-text); text-decoration: none; }
  .footer-nav .sep { margin: 0 8px; }
  .copyright { position: absolute; left: 77px; top: 72px; font-size: 10px; }
  .social { position: absolute; right: 77px; top: 60px; display: flex; align-items: center; font-size: 9px; }
  .social .label { margin-right: 15px; }
  .social .dot { width: 24px; height: 24px; border-radius: 50%; background: var(--dot); margin-left: 5px; }
</style>
</head>
<body>
  <header class="site-header">
    <nav class="main-nav">
      <a href="#" style="left:78px">Home</a>
      <a href="#" style="left:170px">Portfolio</a>
      <a href="#" style="left:275px">Product Specs</a>
      <a href="#" style="left:593px">Testimonials</a>
      <a href="#" style="left:709px">Our Process</a>
      <a href="#" style="left:823px">Contact</a>
    </nav>
    <div class="brand-mark">Brenwick Structures</div>
  </header>

  <section class="hero" role="img" aria-label="Rolled building blueprints, a tablet, calculator and pen on a wooden desk with city high-rises behind"></section>
  <svg class="hero-arrow" style="left:14px" width="46" height="30" viewBox="0 0 46 30"><path d="M14 0 L2 15 L14 30" fill="none" stroke="#fff" stroke-width="1.5" opacity=".8"/><path d="M37 10 L33 15 L37 20" fill="none" stroke="#fff" stroke-width="1.5"/></svg>
  <svg class="hero-arrow" style="left:910px" width="16" height="30" viewBox="0 0 16 30"><path d="M2 0 L14 15 L2 30" fill="none" stroke="#fff" stroke-width="1.5" opacity=".8"/></svg>

  <section class="welcome">
    <h1>WELCOME TO BRENWICK STRUCTURES</h1>
    <h2>On the other hand, we denounce</h2>
    <p>Sed ut perspiciatis unde omnis iste natus error sit voluptatem accusantium doloremque laudantium, totam rem aperiam, eaque ipsa quae ab illo inventore veritatis et quasi architecto beatae vitae dicta sunt explicabo. Nemo enim ipsam voluptatem quia voluptas sit aspernatur aut odit aut fugit, sed quia consequuntur magni dolores eos qui ratione voluptatem sequi nesciunt.vel illum qui dolorem eum fugiat quo voluptas nulla pariatur</p>
    <a class="btn-outline" href="#">READ MORE</a>
  </section>

  <section class="services">
    <div class="service-tile commercial" role="img" aria-label="Commercial high-rise buildings against a blue sky">
      <div class="service-label"><span class="big">COMMERCIAL</span><span class="small">CONSTRUCTION</span></div>
    </div>
    <div class="service-tile residential" role="img" aria-label="Worker in hard hat and safety vest on a building site">
      <div class="service-label"><span class="big">RESIDENTIAL</span><span class="big">BUILDINGS</span></div>
    </div>
  </section>

  <section class="galleries">
    <h3>OUR GALLERIES</h3>
    <div class="gallery-item g1" role="img" aria-label="Plans, hard hat and tape measure on a table with a team in the background"></div>
    <div class="gallery-item g2" role="img" aria-label="Construction site with a yellow crane and concrete columns"></div>
    <div class="gallery-item g3" role="img" aria-label="Two-storey family house at dusk with a front lawn"></div>
    <div class="gallery-item g4" role="img" aria-label="Hands sheltering a small model house"></div>
  </section>

  <footer class="site-footer">
    <div class="footer-brand">Brenwick Structures</div>
    <nav class="footer-nav">
      <a href="#">Home</a><span class="sep">/</span><a href="#">Portfolio</a><span class="sep">/</span><a href="#">Product Specs</a><span class="sep">/</span><a href="#">Testimonials</a><span class="sep">/</span><a href="#">Our Process</a><span class="sep">/</span><a href="#">Contact</a>
    </nav>
    <div class="copyright">Copyright © 2015 Brenwick Structures &nbsp;|&nbsp; All Rights Reserved</div>
    <div class="social">
      <span class="label">Stay Connected:</span>
      <span class="dot"></span><span class="dot"></span><span class="dot"></span><span class="dot"></span>
    </div>
  </footer>
</body>
</html>
```